Advertising for school programs

We're wanting some advertising material for two new programs that we are running in 2022 and 2023. The programs are:
- Zenora Academic Enrichment Program
- Tidewell Athletic
Ideally we would like logos and advertising tiles for each that can be used across social media networks. It would be great to have simple advertising materials, that include the name of the program, a logo for each program, and some text that encourages people to apply.
We'd love to have designs with drawn students, so we don't have to use photos. I've included some photos and our school logo to assist.
A description of the programs is included below to help guide the design - You do not need to include ANY or ALL of the text below in the graphics, I have provided it for context.
A description of both programs below:
Zenora:
The Zenora Academic Enrichment Program is a differentiated pathway that caters specifically for highly capable students.
In the Zenora Academic Enrichment Pathway, students can learn and be assessed at a pace exceeding that of their current year level, with a focus on 21st Century Skills.
For information about the program and application packages, please see the zenora page of our website or contact Marnie Dowse Head of Department Junior School mdows41@brelvan.edu.au
Tidewell Athletic:
In 2022, we will be launching the Tidewell Athletic program to cater for our highly capable athletes.
Tallowmere has long been home to exceptional sporting talent, with multiple state and national representatives in a range of sports and year levels. Tidewell Athletic will provide a differentiated Health and Physical Education curriculum to ensure our student athletes benefit from the latest information on health, wellbeing, fitness and metal health.
The program is open to athletes from all sports and athletic pursuits, as the program is a holistic look at health and athletic performance.
Bursaries:

```html
<!DOCTYPE html>
<html lang="en">
<head>
<meta charset="utf-8">
<title>Zenora and Tidewell Athletic flyer</title>
<link href="https://fonts.googleapis.com/css2?family=Open+Sans:wght@400;600;700;800&family=Oswald:wght@400;500&display=swap" rel="stylesheet">
<style>
:root{
  --navy:#0f4c93;
  --blue:#1b5da8;
  --sky:#4cc3ea;
  --ink:#1f1f1f;
  --white:#ffffff;
  --paper:#f4f5f7;
  --footer:#5e5e5e;
}
*{margin:0;padding:0;box-sizing:border-box}
html,body{width:912px;height:1200px;overflow:hidden;background:var(--white)}
body{font-family:"Open Sans",sans-serif;position:relative}
.flyer{position:absolute;left:31px;top:0;width:850px;height:1200px;background:var(--white);overflow:hidden}
.flyer svg.shapes{position:absolute;left:0;top:0}
.school-name{position:absolute;left:36px;top:150px;width:230px;display:flex;align-items:center;gap:10px;color:var(--navy);font-weight:800;font-size:19px;line-height:1.15}
.school-name .dot{width:16px;height:16px;border-radius:50%;background:var(--navy);flex:none}
.zenora{position:absolute;left:0;top:0;width:850px;height:757px;color:var(--white)}
.zenora h1{position:absolute;top:392px;left:0;width:850px;text-align:center;font-weight:800;font-size:40px;line-height:47px;padding-left:40px}
.ticks{list-style:none}
.ticks li{position:relative;padding-left:24px}
.ticks li svg{position:absolute;left:0;top:4px}
.zenora .col{position:absolute;top:518px;font-size:14.5px;line-height:20px;font-weight:400}
.zenora .col-left{left:72px;width:330px}
.zenora .col-right{left:440px;width:340px}
.info-box{position:absolute;left:68px;top:622px;width:714px;height:93px;border:2px solid var(--sky);border-radius:16px;text-align:center;font-size:17px;line-height:23px;padding-top:14px}
.info-email{position:absolute;left:0;top:697px;width:850px;text-align:center;font-size:20px;font-weight:700;color:var(--sky);padding-left:8px}
.info-email span{background:var(--blue);padding:0 12px}
.tidewell{position:absolute;left:0;top:757px;width:850px;height:390px;background:linear-gradient(180deg,#f7f8fa,#eef0f3)}
.tidewell h2{position:absolute;left:55px;top:26px;font-size:43px;font-weight:800;color:var(--navy);line-height:54px;letter-spacing:-.3px}
.tidewell .rule{position:absolute;left:55px;top:81px;width:396px;height:2px;background:var(--navy)}
.tidewell .lead{position:absolute;left:55px;top:88px;width:420px;font-size:16px;line-height:22px;font-weight:700;color:#2a9bd4}
.tidewell .ticks{position:absolute;left:57px;top:150px;width:400px;font-size:14px;line-height:19.5px;color:var(--ink)}
.tidewell .ticks li + li{margin-top:22px}
.tidewell .ticks li svg{top:3px}
.team-photo{position:absolute;left:503px;top:33px}
.footer{position:absolute;left:0;top:1147px;width:850px;height:53px;background:var(--footer);display:flex;align-items:center;justify-content:center;gap:14px;color:var(--white);font-family:"Oswald",sans-serif;font-size:21px}
.footer .item{display:flex;align-items:center;gap:6px}
.footer .sep{width:1px;height:24px;background:#cfcfcf}
.footer .web b{color:var(--sky);font-weight:500}
.footer .phone{font-weight:500}
</style>
</head>
<body>
<div class="flyer">
  <svg class="shapes" width="850" height="757" viewBox="0 0 850 757">
    <defs>
      <linearGradient id="blueBand" x1="0" y1="0" x2="0" y2="1">
        <stop offset="0" stop-color="#0e4a8f"/>
        <stop offset="1" stop-color="#1d60ab"/>
      </linearGradient>
      <linearGradient id="classroomTone" x1="0" y1="0" x2="1" y2="1">
        <stop offset="0" stop-color="#c79a6a"/>
        <stop offset=".5" stop-color="#5b5f6a"/>
        <stop offset="1" stop-color="#25304a"/>
      </linearGradient>
    </defs>
    <path d="M0,307 L128,392 Q149,406 172,396 L520,232 L850,232 L850,757 L0,757 Z" fill="url(#blueBand)"/>
    <path d="M0,297 L128,382 Q149,396 172,386 L480,240" fill="none" stroke="var(--sky)" stroke-width="1.5"/>
    <path role="img" aria-label="Photo of a smiling student writing at her desk in a classroom" d="M262,0 L850,0 L850,282 L695,380 Q667,398 638,385 L335,228 Q268,190 266,120 Z" fill="url(#classroomTone)" stroke="var(--sky)" stroke-width="9"/>
  </svg>

  <div class="school-name"><span class="dot"></span><span>Tallowmere<br>High School</span></div>

  <section class="zenora">
    <h1>Zenora Academic<br>Enrichment Program</h1>
    <ul class="ticks col col-left">
      <li><svg width="15" height="15" viewBox="0 0 16 16"><circle cx="8" cy="8" r="7" fill="none" stroke="#fff" stroke-width="1.2"/><path d="M4.6,8.2 L7,10.5 L11.4,5.8" fill="none" stroke="#fff" stroke-width="1.3"/></svg>The Zenora Academic Enrichment Program is a differentiated pathway that caters specifically for highly capable students.</li>
    </ul>
    <ul class="ticks col col-right">
      <li><svg width="15" height="15" viewBox="0 0 16 16"><circle cx="8" cy="8" r="7" fill="none" stroke="#fff" stroke-width="1.2"/><path d="M4.6,8.2 L7,10.5 L11.4,5.8" fill="none" stroke="#fff" stroke-width="1.3"/></svg>In the Zenora Academic Enrichment Pathway, students can learn and be assessed at a pace exceeding that of their current year level, with a focus on 21st Century Skills.</li>
    </ul>
    <div class="info-box">For information about the program and application packages, please see the zenora page of our website or contact Marnie Dowse Head of Department Junior School</div>
    <div class="info-email"><span>mdows41@brelvan.edu.au</span></div>
  </section>

  <section class="tidewell">
    <h2>Tidewell Athletic</h2>
    <div class="rule"></div>
    <p class="lead">In 2022, we will be launching the Tidewell Athletic program to cater for our highly capable athletes.</p>
    <ul class="ticks">
      <li><svg width="14" height="14" viewBox="0 0 16 16"><circle cx="8" cy="8" r="7" fill="none" stroke="#1b5da8" stroke-width="1.2"/><path d="M4.6,8.2 L7,10.5 L11.4,5.8" fill="none" stroke="#1b5da8" stroke-width="1.3"/></svg>Tallowmere has long been home to exceptional sporting talent, with multiple state and national representatives in a range of sports and year levels. Tidewell Athletic will provide a differentiated Health and Physical Education curriculum to ensure our student athletes benefit from the latest information on health, wellbeing, fitness and metal health.</li>
      <li><svg width="14" height="14" viewBox="0 0 16 16"><circle cx="8" cy="8" r="7" fill="none" stroke="#1b5da8" stroke-width="1.2"/><path d="M4.6,8.2 L7,10.5 L11.4,5.8" fill="none" stroke="#1b5da8" stroke-width="1.3"/></svg>The program is open to athletes from all sports and athletic pursuits, as the program is a holistic look at health and athletic performance.</li>
    </ul>
    <svg class="team-photo" width="304" height="334" viewBox="0 0 304 334">
      <defs>
        <linearGradient id="teamTone" x1="0" y1="0" x2="0" y2="1">
          <stop offset="0" stop-color="#c9a06a"/>
          <stop offset=".45" stop-color="#2c55a8"/>
          <stop offset="1" stop-color="#173c86"/>
        </linearGradient>
      </defs>
      <path d="M152,2 L296,80 Q302,84 302,92 L302,242 Q302,250 296,254 L152,332 L8,254 Q2,250 2,242 L2,92 Q2,84 8,80 Z" fill="none" stroke="var(--sky)" stroke-width="1.6"/>
      <path role="img" aria-label="Photo of young footballers in blue jerseys in a team huddle" d="M152,16 L282,88 Q288,92 288,100 L288,234 Q288,242 282,246 L152,318 L22,246 Q16,242 16,234 L16,100 Q16,92 22,88 Z" fill="url(#teamTone)"/>
    </svg>
  </section>

  <footer class="footer">
    <span class="item phone"><svg width="18" height="18" viewBox="0 0 24 24"><path d="M6.6,10.8 C8,13.6 10.4,16 13.2,17.4 L15.4,15.2 C15.7,14.9 16.1,14.8 16.4,15 C17.5,15.4 18.7,15.6 20,15.6 C20.6,15.6 21,16 21,16.6 L21,20 C21,20.6 20.6,21 20,21 C10.6,21 3,13.4 3,4 C3,3.4 3.4,3 4,3 L7.5,3 C8.1,3 8.5,3.4 8.5,4 C8.5,5.3 8.7,6.5 9.1,7.6 C9.2,7.9 9.1,8.3 8.9,8.6 Z" fill="var(--sky)"/></svg>(07) 4012 5580</span>
    <span class="sep"></span>
    <span class="item web"><svg width="18" height="18" viewBox="0 0 24 24" fill="none" stroke="var(--sky)" stroke-width="1.5"><circle cx="12" cy="12" r="9"/><ellipse cx="12" cy="12" rx="4" ry="9"/><path d="M3,12 H21 M5,7 H19 M5,17 H19"/></svg>www.<b>tallowmereshs</b>.brelvan.edu.au</span>
  </footer>
</div>
</body>
</html>
```